Business Card Design for Occupational Medicine Start Up Company

We need to design a professional business card. We are a healthcare company providing occupational medicine services to blue collar industries. We are professional, efficient and high quality service providers.

Target Market(s)

Blue Collar Industry: Shipbuilding, Ports, Trucking Companies; The Executives and Safety Officers for these companies

Industry/Entity Type

Healthcare

Contact Information for Business Card

Logo, Name, Title, Email, Phone

Other font styles liked:
• Please match our Brand Guide

Requirements
Must have
• Our Company Colors and Logo

```html
<!DOCTYPE html>
<html lang="en">
<head>
<meta charset="utf-8">
<title>LaborWell Business Card</title>
<link rel="stylesheet" href="https://fonts.googleapis.com/css2?family=Montserrat:wght@400;500;600;700&display=swap">
<style>
  :root {
    --navy: #2e3580;
    --orange: #f2ab4b;
    --paper: #ffffff;
    --page: #ffffff;
    --ink: #2e3580;
    --shadow: rgba(0, 0, 0, 0.18);
  }
  * { margin: 0; padding: 0; box-sizing: border-box; }
  html, body {
    width: 687px;
    height: 1200px;
    overflow: hidden;
    background: var(--page);
    font-family: "Montserrat", sans-serif;
  }
  .sheet {
    position: relative;
    width: 687px;
    height: 1200px;
  }
  .card-slot {
    position: absolute;
    left: 64px;
    width: 560px;
    height: 319px;
    box-shadow: 0 2px 8px var(--shadow);
  }
  .card-slot--front { top: 262px; }
  .card-slot--back { top: 620px; }
  .card {
    position: absolute;
    top: 0;
    left: 0;
    width: 944px;
    height: 538px;
    background: var(--paper);
    transform: scale(0.5932);
    transform-origin: top left;
    overflow: hidden;
  }
  .card__bands {
    position: absolute;
    inset: 0;
    width: 944px;
    height: 538px;
  }
  .band--navy { fill: var(--navy); }
  .band--orange { fill: var(--orange); }

  .brand {
    position: absolute;
    display: flex;
    flex-direction: column;
    align-items: center;
    color: var(--navy);
    font-weight: 600;
    letter-spacing: 0.02em;
    line-height: 1;
  }
  .brand__dot {
    border-radius: 50%;
    background: var(--navy);
  }
  .brand--front {
    left: 0;
    right: 0;
    top: 160px;
    font-size: 62px;
  }
  .brand--front .brand__dot {
    width: 120px;
    height: 120px;
    margin-bottom: 42px;
  }
  .brand--back {
    left: 60px;
    width: 400px;
    top: 190px;
    font-size: 40px;
  }
  .brand--back .brand__dot {
    width: 84px;
    height: 84px;
    margin-bottom: 30px;
  }

  .person {
    position: absolute;
    left: 552px;
    top: 76px;
    color: var(--navy);
  }
  .person__name {
    font-size: 40px;
    font-weight: 400;
    letter-spacing: 0.03em;
    line-height: 1;
  }
  .person__name strong { font-weight: 700; }
  .person__title {
    margin-top: 6px;
    font-size: 17px;
    font-weight: 600;
    letter-spacing: 0.07em;
    color: var(--orange);
  }

  .contacts {
    position: absolute;
    left: 544px;
    top: 200px;
    list-style: none;
    color: var(--ink);
    font-size: 21px;
    font-weight: 500;
    letter-spacing: 0.03em;
    line-height: 28px;
  }
  .contacts__item {
    display: flex;
    align-items: flex-start;
    margin-bottom: 20px;
  }
  .contacts__item--web { margin-top: -4px; }
  .contacts__icon {
    width: 24px;
    height: 24px;
    margin: 2px 30px 0 0;
    flex: none;
    fill: var(--orange);
  }
</style>
</head>
<body>
<main class="sheet">

  <section class="card-slot card-slot--front" aria-label="Business card front">
    <div class="card">
      <svg class="card__bands" viewBox="0 0 944 538" aria-hidden="true">
        <polygon class="band--orange" points="654,0 944,0 944,28 642,28"/>
        <polygon class="band--navy" points="0,0 666,0 654,28 0,28"/>
        <polygon class="band--orange" points="0,490 252,490 210,538 0,538"/>
        <polygon class="band--navy" points="218,509 944,509 944,538 200,538"/>
      </svg>
      <div class="brand brand--front">
        <span class="brand__dot"></span>
        <span class="brand__name">LABORWELL</span>
      </div>
    </div>
  </section>

  <section class="card-slot card-slot--back" aria-label="Business card back">
    <div class="card">
      <svg class="card__bands" viewBox="0 0 944 538" aria-hidden="true">
        <polygon class="band--orange" points="306,0 944,0 944,27 318,27"/>
        <polygon class="band--navy" points="0,0 308,0 320,27 0,27"/>
        <polygon class="band--orange" points="570,473 944,473 944,538 580,538"/>
        <polygon class="band--navy" points="0,497 646,497 665,538 0,538"/>
      </svg>

      <div class="brand brand--back">
        <span class="brand__dot"></span>
        <span class="brand__name">LABORWELL</span>
      </div>

      <div class="person">
        <p class="person__name"><strong>DANA</strong> HOLLOWAY</p>
        <p class="person__title">CHIEF EXECUTIVE OFFICER</p>
      </div>

      <ul class="contacts">
        <li class="contacts__item">
          <svg class="contacts__icon" viewBox="0 0 24 24" aria-hidden="true"><path d="M6.6 10.8a15 15 0 0 0 6.6 6.6l2.2-2.2a1 1 0 0 1 1-.25 11.4 11.4 0 0 0 3.6.57 1 1 0 0 1 1 1V20a1 1 0 0 1-1 1A17 17 0 0 1 3 4a1 1 0 0 1 1-1h3.5a1 1 0 0 1 1 1c0 1.25.2 2.45.57 3.6a1 1 0 0 1-.25 1z"/></svg>
          <span>+1 (555) 210-3874</span>
        </li>
        <li class="contacts__item">
          <svg class="contacts__icon" viewBox="0 0 24 24" aria-hidden="true"><path d="M2 5h20v14H2z M2 5l10 8 10-8" fill="var(--orange)"/><path d="M2 6l10 7.5L22 6" fill="none" stroke="#fff" stroke-width="1.6"/></svg>
          <span>info@laborwellhealth.com</span>
        </li>
        <li class="contacts__item">
          <svg class="contacts__icon" viewBox="0 0 24 24" aria-hidden="true"><path d="M12 1.5a7.5 7.5 0 0 0-7.5 7.5c0 5.6 7.5 13.5 7.5 13.5s7.5-7.9 7.5-13.5A7.5 7.5 0 0 0 12 1.5zm0 10.5a3 3 0 1 1 0-6 3 3 0 0 1 0 6z"/></svg>
          <span>Harbor Road 410, 8th<br>Floor Norfolk -<br>United States</span>
        </li>
        <li class="contacts__item contacts__item--web">
          <svg class="contacts__icon" viewBox="0 0 24 24" aria-hidden="true"><circle cx="12" cy="12" r="10"/><g fill="none" stroke="#fff" stroke-width="1.2"><ellipse cx="12" cy="12" rx="4.5" ry="10"/><path d="M2 12h20M4 7h16M4 17h16M12 2v20"/></g></svg>
          <span>www.laborwellhealth.com</span>
        </li>
      </ul>
    </div>
  </section>

</main>
</body>
</html>
```